Mindfulness School for Children -- Business Cards

We're looking for business cards for our school directors and owners. We're a mindfulness school for children called little lanterns. Attached are our logos/icons.

```html
<!DOCTYPE html>
<html lang="en">
<head>
<meta charset="utf-8">
<title>little lanterns — Business Cards</title>
<link href="https://fonts.googleapis.com/css2?family=Alegreya:wght@400&family=Arimo:wght@400;700&display=swap" rel="stylesheet">
<style>
  :root {
    --backdrop: #e9e9eb;
    --card-white: #ffffff;
    --teal: #2a9bb5;
    --text-grey: #6f6f72;
    --rule-grey: #b9b9bb;
    --ink: #1c1c1c;
    --wash-blue: #6fa9bd;
    --wash-aqua: #9fcfcf;
    --wash-mint: #bfe0cf;
    --logo-green: #5aa88c;
  }
  * { margin: 0; padding: 0; box-sizing: border-box; }
  html, body { width: 1200px; height: 802px; overflow: hidden; }
  body {
    background: var(--backdrop);
    position: relative;
    font-family: "Arimo", Arial, sans-serif;
  }
  .card {
    position: absolute;
    top: 258px;
    width: 500px;
    height: 286px;
    box-shadow: 0 6px 18px rgba(0,0,0,0.12);
    overflow: hidden;
  }
  .card--front { left: 70px; background: var(--card-white); }
  .card--back { left: 630px; }

  .brand {
    font-family: "Alegreya", Georgia, serif;
    font-weight: 400;
    letter-spacing: -0.5px;
    white-space: nowrap;
  }
  .card--front .brand {
    position: absolute;
    left: 40px;
    top: 150px;
    font-size: 40px;
    color: var(--logo-green);
    display: flex;
    align-items: center;
    gap: 10px;
  }
  .brand-dot {
    width: 12px; height: 12px;
    border-radius: 50%;
    background: var(--teal);
  }
  .divider {
    position: absolute;
    left: 292px;
    top: 44px;
    width: 1px;
    height: 198px;
    background: var(--rule-grey);
  }
  .contact {
    position: absolute;
    left: 312px;
    top: 52px;
    color: var(--text-grey);
    font-size: 12.5px;
    line-height: 1.35;
  }
  .contact__name {
    color: var(--teal);
    font-weight: 700;
    font-size: 19px;
    letter-spacing: 0.3px;
    line-height: 1.1;
  }
  .contact__role { margin-bottom: 14px; }
  .contact__address { margin-bottom: 12px; }
  .contact__line {
    display: flex;
    align-items: center;
    gap: 8px;
    margin-bottom: 3px;
  }
  .contact__line svg { width: 12px; height: 12px; flex: none; }

  .wash {
    position: absolute; inset: 0;
    background:
      radial-gradient(ellipse at 65% 45%, var(--wash-mint) 0%, transparent 45%),
      radial-gradient(ellipse at 20% 85%, var(--wash-blue) 0%, transparent 55%),
      radial-gradient(ellipse at 85% 15%, var(--wash-aqua) 0%, transparent 60%),
      linear-gradient(160deg, var(--wash-blue) 0%, var(--wash-aqua) 55%, var(--wash-mint) 100%);
  }
  .card--back .brand {
    position: absolute;
    left: 0; right: 0;
    top: 118px;
    text-align: center;
    font-size: 42px;
    color: var(--ink);
  }
</style>
</head>
<body>

<section class="card card--front" aria-label="Business card front">
  <div class="brand"><span class="brand-dot"></span>little lanterns</div>
  <div class="divider"></div>
  <div class="contact">
    <div class="contact__name">MAYA ELLISON</div>
    <div class="contact__role">Manager</div>
    <div class="contact__address">Your Address, City<br>State, Zip 0000</div>
    <div class="contact__line">
      <svg viewBox="0 0 12 12"><circle cx="6" cy="6" r="6" fill="#2a9bb5"/><path d="M3.6 3.2l1.2-.4.7 1.6-.7.5c.4.9 1 1.5 1.9 1.9l.5-.7 1.6.7-.4 1.2C6 8.1 3.9 6 3.6 3.2z" fill="#fff"/></svg>
      <span>555-014-2100</span>
    </div>
    <div class="contact__line">
      <svg viewBox="0 0 12 12"><rect x="0.5" y="2.5" width="11" height="7" fill="#2a9bb5"/><path d="M0.8 2.8L6 6.8l5.2-4" fill="none" stroke="#fff" stroke-width="0.9"/></svg>
      <span>hello@littlelanterns.org</span>
    </div>
    <div class="contact__line">
      <svg viewBox="0 0 12 12"><circle cx="6" cy="6" r="6" fill="#2a9bb5"/><circle cx="6" cy="6" r="3.6" fill="none" stroke="#fff" stroke-width="0.8"/><path d="M2.4 6h7.2M6 2.4v7.2" stroke="#fff" stroke-width="0.8"/></svg>
      <span>www.littlelanterns.org</span>
    </div>
  </div>
</section>

<section class="card card--back" aria-label="Business card back">
  <div class="wash" role="img" aria-label="Soft blue and mint watercolour wash background"></div>
  <div class="brand">little lanterns</div>
</section>

</body>
</html>
```